Business Card Design for Occupational Medicine Start Up Company

We need to design a professional business card. We are a healthcare company providing occupational medicine services to blue collar industries. We are professional, efficient and high quality service providers.

Target Market(s)

Blue Collar Industry: Shipbuilding, Ports, Trucking Companies; The Executives and Safety Officers for these companies

Industry/Entity Type

Healthcare

Contact Information for Business Card

Logo, Name, Title, Email, Phone

Other font styles liked:
• Please match our Brand Guide

Requirements
Must have
• Our Company Colors and Logo

```html
<!DOCTYPE html>
<html lang="en">
<head>
<meta charset="utf-8">
<title>Harborline Health – Business Card</title>
<link href="https://fonts.googleapis.com/css2?family=Catamaran:wght@600&family=Hind:wght@400;600;700&display=swap" rel="stylesheet">
<style>
  :root {
    --bg: #e9eaec;
    --navy: #2b3488;
    --navy-dark: #262c7c;
    --navy-light: #3b4aa3;
    --gold: #f5c47c;
    --ink: #3b3f57;
    --muted: #5b5e68;
    --white: #ffffff;
  }
  * { margin: 0; padding: 0; box-sizing: border-box; }
  html, body { width: 1200px; height: 1200px; overflow: hidden; background: var(--bg); }
  body { position: relative; font-family: "Hind", sans-serif; }

  .card { position: absolute; left: 222px; width: 756px; height: 463px; }

  /* Front */
  .card-front { top: 109px; background: var(--white); }
  .brand { position: absolute; left: 50px; top: 160px; width: 300px; text-align: center; }
  .brand-dot { display: block; width: 84px; height: 84px; margin: 0 auto 22px; border-radius: 50%; background: var(--navy); }
  .brand-name { font-family: "Hind", sans-serif; font-weight: 700; font-size: 31px; letter-spacing: 1px; color: var(--navy); line-height: 1; white-space: nowrap; }
  .divider { position: absolute; left: 389px; top: 133px; width: 3px; height: 214px; background: var(--gold); }
  .person { position: absolute; left: 432px; top: 130px; }
  .person-name { font-family: "Catamaran", sans-serif; font-weight: 600; font-size: 43px; color: var(--navy); line-height: 1.05; }
  .person-title { font-size: 23px; color: var(--muted); line-height: 1.2; margin-top: 2px; }
  .contacts { list-style: none; margin-top: 30px; }
  .contacts li { display: flex; align-items: center; height: 31px; font-size: 21px; color: var(--ink); }
  .contacts svg { width: 20px; height: 20px; margin-right: 12px; flex: none; fill: var(--navy); }
  .address-band { position: absolute; left: 0; bottom: 0; width: 100%; height: 67px; background: var(--navy); color: var(--white); font-size: 22px; display: flex; align-items: center; justify-content: center; padding-top: 4px; }

  /* Back */
  .card-back { top: 630px; background: linear-gradient(135deg, var(--navy-dark) 0%, var(--navy) 55%, var(--navy-light) 100%); }
  .back-pattern { position: absolute; inset: 0; background: linear-gradient(135deg, rgba(255,255,255,0.03), rgba(255,255,255,0.07)); }
  .back-brand { position: absolute; right: 66px; bottom: 70px; display: flex; align-items: center; gap: 8px; }
  .back-dot { width: 16px; height: 16px; border-radius: 50%; background: var(--white); }
  .back-name { font-weight: 700; font-size: 15px; letter-spacing: 1px; color: var(--white); }
</style>
</head>
<body>

<section class="card card-front">
  <div class="brand">
    <span class="brand-dot"></span>
    <p class="brand-name">HARBORLINE HEALTH</p>
  </div>

  <div class="divider"></div>

  <div class="person">
    <h1 class="person-name">Marcus Delaney</h1>
    <p class="person-title">Account Executive</p>
    <ul class="contacts">
      <li>
        <svg viewBox="0 0 24 24" aria-hidden="true"><path d="M6.6 10.8c1.4 2.8 3.8 5.1 6.6 6.6l2.2-2.2c.3-.3.7-.4 1-.2 1.1.4 2.3.6 3.6.6.6 0 1 .4 1 1V20c0 .6-.4 1-1 1C10.6 21 3 13.4 3 4c0-.6.4-1 1-1h3.5c.6 0 1 .4 1 1 0 1.3.2 2.5.6 3.6.1.3 0 .7-.2 1z"/></svg>
        415.555.0142
      </li>
      <li>
        <svg viewBox="0 0 24 24" aria-hidden="true"><path d="M6 2h12v5H6zM4 8h16a2 2 0 0 1 2 2v7h-4v5H6v-5H2v-7a2 2 0 0 1 2-2zm4 8v4h8v-4z"/></svg>
        415.555.0187
      </li>
      <li>
        <svg viewBox="0 0 24 24" aria-hidden="true"><path d="M2 4h20v9.5a6 6 0 0 0-8.5 6.5H2zm2 2v.3l8 5.2 8-5.2V6zM18 14a4 4 0 1 1 0 8 4 4 0 0 1 0-8zm-1.6 3.4-.9.9 1.8 1.8 3-3-.9-.9-2.1 2.1z"/></svg>
        mdelaney@harborline.com
      </li>
      <li>
        <svg viewBox="0 0 24 24" aria-hidden="true" fill="none"><g fill="none" stroke="#2b3488" stroke-width="1.6"><circle cx="12" cy="12" r="9.5"/><ellipse cx="12" cy="12" rx="4.2" ry="9.5"/><path d="M2.5 12h19M4 7h16M4 17h16"/></g></svg>
        www.harborline.com
      </li>
    </ul>
  </div>

  <div class="address-band">48 Pier Avenue Suite 210 San Francisco, CA 94107</div>
</section>

<section class="card card-back">
  <div class="back-pattern" role="img" aria-label="Subtle embossed repeating brand pattern across the card back"></div>
  <div class="back-brand">
    <span class="back-dot"></span>
    <span class="back-name">HARBORLINE</span>
  </div>
</section>

</body>
</html>
```